Flyer Design for Private Car Service

Flyer should cater to Business Travelers and Executives who travel Business Class or First Class.
Flyer should include images attached.
Flyer should include the below text
Dallas to Austin
Chauffeured SUVs
• Travel Dallas to Austin in a new 2025 Norvak Tressel for $499 one-way
• Trip includes a Uniformed Chauffeur who has a Commercial Drivers License (CDL)
• You can Schedule Chauffeur Pickup at Your Home in Dallas
• Our Chauffeur will Drop You Off at Your Final Destination in Austin
• You can Schedule Chauffeur Return Pickup in Austin and Return Back to Dallas.
• We offer Faster Times on Door-to-Door Travel than Bluequill Airways
• We offer Comparable Prices on Door-to-Door Travel Times than Bluequill Airways
• All of our trips are insured with $500k of commercial auto insurance
• Our Passengers can Talk on Cell Phone & Conduct Kavlo calls Throughout Travel
• Our Passengers have Maximum Privacy, Comfort and First-Class Amenities.
• Our Passengers Avoid Marrow Pike Airfield and QHN Airport hassles & delays
• Member Tellbrook Chamber of Commerce, Pindle Chamber of Commerce.
• Book your trip today at www.quorvanride.example
Target Market(s)
Business Travelers
Look and feel

```html
<!DOCTYPE html>
<html lang="en">
<head>
<meta charset="utf-8">
<title>Dallas to Austin Chauffeured SUVs</title>
<link rel="stylesheet" href="https://fonts.googleapis.com/css2?family=Playfair+Display:wght@700;900&family=Roboto:wght@400;500&display=swap">
<style>
  :root {
    --ink: #231f20;
    --ink-deep: #161314;
    --red: #e9262a;
    --red-bright: #ef3346;
    --white: #ffffff;
    --photo-warm: #5a5452;
    --photo-cool: #8d9092;
  }
  * { margin: 0; padding: 0; box-sizing: border-box; }
  html, body { width: 927px; height: 1200px; overflow: hidden; background: var(--ink); }
  .flyer {
    position: relative;
    width: 927px;
    height: 1200px;
    overflow: hidden;
    background: var(--ink);
    font-family: "Roboto", Arial, sans-serif;
    color: var(--white);
  }
  .shapes { position: absolute; inset: 0; }
  .brand {
    position: absolute;
    left: 410px;
    top: 118px;
    width: 416px;
    text-align: center;
    font-family: "Roboto", Arial, sans-serif;
    font-weight: 400;
    font-size: 44px;
    letter-spacing: 3px;
    color: var(--white);
  }
  .headline { position: absolute; left: 320px; top: 212px; width: 607px; height: 266px; }
  .headline text { font-family: "Playfair Display", Georgia, serif; font-weight: 900; }
  .features {
    position: absolute;
    left: 30px;
    top: 573px;
    list-style: none;
    font-size: 15.6px;
    font-weight: 500;
    line-height: 32px;
  }
  .features li { display: flex; align-items: center; white-space: nowrap; }
  .features li::before {
    content: "";
    width: 18px;
    height: 1.5px;
    background: var(--red);
    margin-right: 4px;
  }
  .features li span::before { content: "• "; }
  .cta { position: absolute; left: 215px; top: 984px; display: flex; align-items: center; gap: 29px; }
  .cta-icon {
    width: 83px; height: 83px; border-radius: 50%;
    background: radial-gradient(circle at 40% 30%, #f5525a, var(--red) 70%);
    display: flex; align-items: center; justify-content: center;
  }
  .cta-text { font-family: "Roboto", Arial, sans-serif; font-weight: 500; line-height: 46px; margin-top: -4px; }
  .cta-lead { font-size: 35px; color: var(--white); }
  .cta-url { font-size: 35px; color: var(--red-bright); }
</style>
</head>
<body>
<div class="flyer">
  <svg class="shapes" width="927" height="1200" viewBox="0 0 927 1200" xmlns="http://www.w3.org/2000/svg">
    <defs>
      <linearGradient id="stripFade" x1="0" y1="0" x2="0" y2="1">
        <stop offset="0" stop-color="#231f20"/>
        <stop offset="0.35" stop-color="#3a3738"/>
        <stop offset="1" stop-color="#4b4748"/>
      </linearGradient>
      <radialGradient id="leftPhoto" cx="0.45" cy="0.45" r="0.6">
        <stop offset="0" stop-color="#7a7472"/>
        <stop offset="1" stop-color="#2e2a2b"/>
      </radialGradient>
      <radialGradient id="rightPhoto" cx="0.4" cy="0.3" r="0.7">
        <stop offset="0" stop-color="#dfe3e4"/>
        <stop offset="0.6" stop-color="#8a8d8f"/>
        <stop offset="1" stop-color="#2c2a2b"/>
      </radialGradient>
    </defs>

    <rect class="headline-band" x="320" y="212" width="607" height="266" fill="#e9262a"/>

    <line x1="432" y1="92" x2="806" y2="92" stroke="#e9262a" stroke-width="1" opacity="0.6"/>
    <line x1="525" y1="177" x2="565" y2="177" stroke="#e9262a" stroke-width="1"/>
    <line x1="675" y1="177" x2="715" y2="177" stroke="#e9262a" stroke-width="1"/>

    <g role="img" aria-label="Uniformed chauffeur assisting a business traveler with luggage beside a black SUV">
      <circle cx="76" cy="273" r="238" fill="url(#leftPhoto)"/>
    </g>
    <circle cx="70" cy="302" r="240" fill="none" stroke="#e9262a" stroke-width="3"/>

    <g role="img" aria-label="Two uniformed chauffeurs in caps standing outdoors">
      <circle cx="902" cy="676" r="220" fill="url(#rightPhoto)"/>
    </g>
    <circle cx="909" cy="687" r="243" fill="none" stroke="#e9262a" stroke-width="3"/>

    <g role="img" aria-label="Fleet of black, white and red SUVs with chauffeurs standing between them">
      <rect x="0" y="1060" width="927" height="140" fill="url(#stripFade)"/>
    </g>
  </svg>

  <div class="brand">Quorvan Ride</div>

  <svg class="headline" viewBox="0 0 607 266" xmlns="http://www.w3.org/2000/svg">
    <text x="309" y="80" text-anchor="middle" font-size="52" textLength="512" lengthAdjust="spacingAndGlyphs" fill="#231f20" stroke="#ffffff" stroke-width="1.2" paint-order="stroke">DALLAS TO AUSTIN</text>
    <text x="302" y="152" text-anchor="middle" font-size="68" textLength="502" lengthAdjust="spacingAndGlyphs" fill="#ffffff">CHAUFFEURED</text>
    <text x="309" y="225" text-anchor="middle" font-size="68" textLength="158" lengthAdjust="spacingAndGlyphs" fill="#ffffff">SUVS</text>
  </svg>

  <ul class="features">
    <li><span>Travel Dallas to Austin in a new 2025 Norvak Tressel for $499 one-way</span></li>
    <li><span>Trip includes a Uniformed Chauffeur who has a Commercial Drivers License (CDL)</span></li>
    <li><span>You can Schedule Chauffeur Pickup at Your Home in Dallas</span></li>
    <li><span>Our Chauffeur will Drop You Off at Your Final Destination in Austin</span></li>
    <li><span>You can Schedule Chauffeur Return Pickup in Austin and Return Back to Dallas.</span></li>
    <li><span>We offer Faster Times on Door-to-Door Travel than Bluequill Airways</span></li>
    <li><span>We offer Comparable Prices on Door-to-Door Travel Times than Bluequill Airways</span></li>
    <li><span>All of our trips are insured with $500k of commercial auto insurance</span></li>
    <li><span>Our Passengers can Talk on Cell Phone &amp; Conduct Kavlo calls Throughout Travel</span></li>
    <li><span>Our Passengers have Maximum Privacy, Comfort and First-Class Amenities.</span></li>
    <li><span>Our Passengers Avoid Marrow Pike Airfield and QHN Airport hassles &amp; delays</span></li>
    <li><span>Member Tellbrook Chamber of Commerce, Pindle Chamber of Commerce.</span></li>
  </ul>

  <div class="cta">
    <div class="cta-icon">
      <svg width="30" height="30" viewBox="0 0 30 30" xmlns="http://www.w3.org/2000/svg" aria-hidden="true">
        <g fill="none" stroke="#ffffff" stroke-width="2.4">
          <circle cx="15" cy="15" r="12.5"/>
          <ellipse cx="15" cy="15" rx="5.5" ry="12.5"/>
          <line x1="2.5" y1="15" x2="27.5" y2="15"/>
          <line x1="4.5" y1="9" x2="25.5" y2="9"/>
          <line x1="4.5" y1="21" x2="25.5" y2="21"/>
        </g>
      </svg>
    </div>
    <div class="cta-text">
      <div class="cta-lead">Book your trip today at</div>
      <div class="cta-url">www.quorvanride.example</div>
    </div>
  </div>
</div>
</body>
</html>
```